Australian Trucking Company Requires Professional Looking Stationary

We require a professional looking stationary design that incorporates our newly designed logo.

Our business, called "Brell Haulage Contracting", provides contracting work, transport and logistics to business in Western Australia particularly with links to the mining sector.

We are a small business looking to expand and our new logo and our new stationary will help develop our brand image in our market place.

Target Market(s)

Businesses and Corporation with links to the Mining Sector

Industry/Entity Type

Small Business

Requirements
Must have
• The letterhead must have the following details:
The new logo

Text saying: "Brell Holdings Pty Ltd (ACN 582 316 907) ATF The Brell Discretionary Trust T/AS"
"ABN 71 834 209 553"
Address "P.O Box 817 Wattlegrove WA, 6958"
Phone: 08 9352 7140
Email: brellhaul@mailbox-example.com.au

The text on the letterhead should be editable as the details are likely to change in the near future. Provision should be made for a website address all though one isn't available at the moment.

The styling, layout and font text is entirely up to the designer.

```html
<!DOCTYPE html>
<html lang="en">
<head>
<meta charset="utf-8">
<title>Brell Haulage Contracting – Business Card</title>
<link rel="stylesheet" href="https://fonts.googleapis.com/css2?family=Roboto:wght@400;700;900&display=swap">
<style>
  :root {
    --page: #ebe8e3;
    --card: #ffffff;
    --brand-red: #a41c22;
    --text-red: #8b1a1f;
    --band: #4a4a4a;
    --mark-grey: #6b6b6b;
    --ink-grey: #444444;
  }
  * { margin: 0; padding: 0; box-sizing: border-box; }
  html, body {
    width: 1200px; height: 1200px; overflow: hidden;
    background: var(--page);
    font-family: "Roboto", Arial, sans-serif;
  }
  .canvas { position: relative; width: 1200px; height: 1200px; }
  .card {
    position: absolute; width: 840px; height: 480px;
    background: var(--card);
    box-shadow: 0 2px 8px rgba(0,0,0,0.12);
  }
  .card--front { left: 84px; top: 78px; }
  .card--back { left: 284px; top: 650px; }

  /* front */
  .brand {
    position: absolute; left: 76px; top: 58px;
    display: flex; align-items: center; gap: 38px;
  }
  .brand__mark {
    width: 150px; height: 150px; background: var(--mark-grey);
  }
  .brand__name {
    color: var(--brand-red); font-weight: 900;
    font-size: 44px; line-height: 52px; text-transform: uppercase;
    letter-spacing: 1px;
  }
  .name-band {
    position: absolute; left: 0; top: 277px; width: 100%; height: 53px;
    background: var(--band); color: #fff;
    display: flex; align-items: center; justify-content: center; gap: 28px;
  }
  .name-band__name { font-weight: 700; font-size: 29px; }
  .name-band__sep { font-weight: 700; font-size: 26px; }
  .name-band__title { font-size: 24px; letter-spacing: 2.5px; }
  .details {
    position: absolute; left: 0; top: 356px; width: 100%;
    color: var(--text-red); font-size: 18px; text-align: center;
  }
  .details__line { height: 38px; line-height: 28px; }
  .details__contacts {
    display: flex; justify-content: center; gap: 30px;
  }
  .contact { display: inline-flex; align-items: center; gap: 7px; }
  .contact svg { width: 15px; height: 15px; }

  /* back */
  .back-brand {
    position: absolute; left: 0; top: 95px; width: 100%;
    display: flex; flex-direction: column; align-items: center; gap: 26px;
  }
  .back-brand__mark { width: 160px; height: 160px; background: var(--mark-grey); }
  .back-brand__name {
    color: var(--ink-grey); font-weight: 700; font-size: 30px;
    text-transform: uppercase; letter-spacing: 2px;
  }
  .web-address {
    position: absolute; left: 0; top: 386px; width: 100%; text-align: center;
    font-size: 29px; letter-spacing: 3px; color: var(--ink-grey);
  }
  .web-address__domain { color: var(--brand-red); font-weight: 900; }
</style>
</head>
<body>
<main class="canvas">
  <section class="card card--front">
    <div class="brand">
      <div class="brand__mark" aria-hidden="true"></div>
      <div class="brand__name">Brell<br>Haulage<br>Contracting</div>
    </div>
    <div class="name-band">
      <span class="name-band__name">Your Name</span>
      <span class="name-band__sep">/</span>
      <span class="name-band__title">Title</span>
    </div>
    <div class="details">
      <p class="details__line">P.O Box 817 Wattlegrove WA, 6958</p>
      <p class="details__line details__contacts">
        <span class="contact">
          <svg viewBox="0 0 16 16" aria-hidden="true"><circle cx="8" cy="8" r="7" fill="none" stroke="currentColor" stroke-width="1.3"/><path d="M5.5 4.5c-.8 2.8.8 6 3.8 7l1.2-1.6-1.6-1-.8.7c-1-.5-1.6-1.5-1.8-2.6l1-.5-.4-1.8z" fill="currentColor"/></svg>
          08 9352 7140
        </span>
        <span class="contact">
          <svg viewBox="0 0 16 16" aria-hidden="true"><rect x="1" y="3.5" width="14" height="9" fill="currentColor"/><path d="M1 3.5l7 5 7-5" fill="none" stroke="#fff" stroke-width="1.2"/></svg>
          brellhaul@mailbox-example.com.au
        </span>
        <span class="contact">
          <svg viewBox="0 0 16 16" aria-hidden="true" fill="none" stroke="currentColor" stroke-width="1.1"><circle cx="8" cy="8" r="6.5"/><ellipse cx="8" cy="8" rx="3" ry="6.5"/><path d="M1.5 8h13M2.5 5h11M2.5 11h11"/></svg>
          www.brellhaulage.com
        </span>
      </p>
      <p class="details__line">Brell Holdings Pty Ltd (ACN 582 316 907) ATF The Brell Discretionary Trust T/AS</p>
    </div>
  </section>

  <section class="card card--back">
    <div class="back-brand">
      <div class="back-brand__mark" aria-hidden="true"></div>
      <div class="back-brand__name">Brell Haulage Contracting</div>
    </div>
    <p class="web-address">www.<span class="web-address__domain">brellhaulage</span>.com</p>
  </section>
</main>
</body>
</html>
```